Business card for Sports Apparel business

DOUBLE SIDED DESIGN
We need business cards for a new sports apparel business. We are developing a protective headband for soccer initially.
Torvalle is focused on designing and developing head protection products to reduce the likelihood of concussion when playing sports. Exploring and understanding medical insights, material science research, current and former players experiences and governing bodies guidelines has allowed Torvalle to develop the safety, style, form and function requirements of a suitable product to bring to market.
Target Market(s)
Mums buying kits for the sons and daughters. Amateur footballers.
Industry/Entity Type
Sporting Good
Contact Information for Business Card
Martin Ashworth - CEO
Mobile: +44 7431589027
Email: martin@torvalle.co.uk
Tel: 0208 5519372
Helena Pargeter - COO
Mob: +44 7385 640117
Email: helena@torvalle.co.uk
Tel: 0208 5519372
Duncan Farrow - CCO
Mob: +44 7564 293081
Email: duncan@torvalle.co.uk
Tel: 0208 5519372
Look and feel
Each slider illustrates characteristics of the customer's brand and the style your logo design should communicate.

```html
<!DOCTYPE html>
<html lang="en">
<head>
<meta charset="utf-8">
<title>Torvalle Business Card</title>
<link href="https://fonts.googleapis.com/css2?family=Montserrat:wght@400;700&display=swap" rel="stylesheet">
<style>
  :root {
    --backdrop: #2b2b2b;
    --card-white: #ffffff;
    --brand-blue: #135f93;
    --brand-grey: #666666;
    --text-grey: #6f6f6f;
    --rule-grey: #8a8a8a;
  }
  * { box-sizing: border-box; margin: 0; padding: 0; }
  html, body { width: 1200px; height: 900px; overflow: hidden; }
  body {
    background: var(--backdrop);
    font-family: "Montserrat", sans-serif;
    position: relative;
  }
  .card {
    position: absolute;
    left: 240px;
    width: 720px;
    height: 395px;
    overflow: hidden;
    background: var(--card-white);
  }
  .card--front { top: 45px; }
  .card--back { top: 465px; }

  /* Front side: two colour fields with the name in the white band between */
  .front-field {
    position: absolute;
    top: 45px;
    bottom: 45px;
  }
  .front-field--grey { left: 0; width: 230px; background: var(--brand-grey); }
  .front-field--blue { right: 0; width: 230px; background: var(--brand-blue); }
  .front-name {
    position: absolute;
    left: 230px;
    width: 260px;
    top: 50%;
    transform: translateY(-50%);
    text-align: center;
    font-weight: 700;
    font-size: 30px;
    letter-spacing: 2px;
    color: var(--brand-grey);
    text-transform: uppercase;
    z-index: 1;
  }

  /* Back side */
  .brand-mark {
    position: absolute;
    left: 28px;
    top: 92px;
    display: flex;
    align-items: center;
    gap: 12px;
  }
  .brand-mark__square {
    width: 26px; height: 26px;
    background: var(--brand-blue);
  }
  .brand-mark__name {
    font-weight: 700;
    font-size: 36px;
    letter-spacing: 1px;
    color: var(--brand-grey);
    text-transform: uppercase;
  }
  .divider {
    position: absolute;
    left: 0;
    top: 190px;
    width: 560px;
    height: 2px;
    background: var(--rule-grey);
  }
  .person {
    position: absolute;
    left: 400px;
    top: 136px;
  }
  .person__name {
    font-weight: 700;
    font-size: 22px;
    letter-spacing: 1px;
    color: var(--brand-blue);
    text-transform: uppercase;
    line-height: 1;
  }
  .person__role {
    font-size: 17px;
    color: var(--text-grey);
    line-height: 1.1;
    margin-top: 2px;
  }
  .contacts {
    position: absolute;
    left: 400px;
    top: 232px;
    list-style: none;
  }
  .contacts__item {
    display: flex;
    align-items: center;
    gap: 10px;
    font-size: 19px;
    color: var(--text-grey);
    line-height: 30px;
  }
  .contacts__icon { width: 18px; height: 18px; flex: none; }
</style>
</head>
<body>
  <section class="card card--front" aria-label="Card front">
    <div class="front-field front-field--grey"></div>
    <div class="front-field front-field--blue"></div>
    <p class="front-name">Torvalle</p>
  </section>

  <section class="card card--back" aria-label="Card back">
    <div class="brand-mark">
      <span class="brand-mark__square"></span>
      <span class="brand-mark__name">Torvalle</span>
    </div>

    <div class="divider"></div>

    <div class="person">
      <p class="person__name">Martin Ashworth</p>
      <p class="person__role">CEO</p>
    </div>

    <ul class="contacts">
      <li class="contacts__item">
        <svg class="contacts__icon" viewBox="0 0 18 18" aria-hidden="true">
          <rect x="5" y="1.5" width="8" height="15" rx="1.5" fill="none" stroke="#135f93" stroke-width="1.6"/>
          <line x1="8" y1="14" x2="10" y2="14" stroke="#135f93" stroke-width="1.6"/>
        </svg>
        <span>0208 551 9372</span>
      </li>
      <li class="contacts__item">
        <svg class="contacts__icon" viewBox="0 0 18 18" aria-hidden="true">
          <path d="M4 2 L7 5 L5.5 7 C6.5 9.5 8.5 11.5 11 12.5 L13 11 L16 14 L14 16 C8 15.5 2.5 10 2 4 Z" fill="none" stroke="#135f93" stroke-width="1.4" stroke-linejoin="round"/>
        </svg>
        <span>+44 7431589027</span>
      </li>
      <li class="contacts__item">
        <svg class="contacts__icon" viewBox="0 0 18 18" aria-hidden="true">
          <rect x="1.5" y="4" width="15" height="10" fill="none" stroke="#135f93" stroke-width="1.5"/>
          <polyline points="1.5,4 9,10 16.5,4" fill="none" stroke="#135f93" stroke-width="1.5"/>
        </svg>
        <span>martin@torvalle.co.uk</span>
      </li>
    </ul>
  </section>
</body>
</html>
```